Business Card and Letterhead for Pimlu - modern real estate business

I need a double sided business card design for Pimlu. Please see business card brief here https://files.trelvonadocs.com/sheet/r/7QzTmWbaXLJnoPEd-kRyUgFhHsstbvCe2qfoMxDa_pz/view?mode=shared

Please feel free to design the business cards however you feel best. I am happy to give some creative freedoms and then provide feedback from there.

Please then also create a letterhead to match the business card design

Colors

Designer to choose colors to be used in the design.

Requirements
Must have
• Must be a modern, elegant business card which looks very professional

```html
<!DOCTYPE html>
<html lang="en">
<head>
<meta charset="utf-8">
<title>Pimlu Stationery</title>
<link href="https://fonts.googleapis.com/css2?family=Lato:wght@400;700;900&display=swap" rel="stylesheet">
<style>
:root{
  --stage:#ece9e4;
  --paper:#ffffff;
  --ink:#1a1a1a;
  --card:#1c1b1c;
  --card-deep:#121112;
  --red:#e3262d;
  --muted:#c9c9c9;
  --rule:#5a5a5a;
}
*{margin:0;padding:0;box-sizing:border-box}
html,body{width:1200px;height:900px;overflow:hidden}
body{background:var(--stage);font-family:'Lato',sans-serif;position:relative}

.letterhead{position:absolute;left:45px;top:112px;width:494px;height:698px;background:var(--paper);box-shadow:0 4px 12px rgba(0,0,0,.18)}
.letterhead .brand{position:absolute;left:37px;top:22px;font-size:42px;font-weight:700;letter-spacing:2px;color:var(--red);line-height:1}
.letter-body{position:absolute;left:47px;width:401px;color:var(--ink);font-size:9.6px;line-height:12px;text-align:justify}
.salutation{top:176px}
.para-1{top:206px}
.para-2{top:290px}
.para-3{top:362px}
.para-4{top:433px}
.signoff{position:absolute;left:47px;top:482px;font-size:9.6px;line-height:13px;color:var(--ink)}
.letter-rule{position:absolute;left:0;right:0;top:658px;height:3px;background:var(--red)}
.letter-footer{position:absolute;left:0;right:0;top:666px;height:32px;background:var(--ink);color:#fff;font-size:10px;display:flex;align-items:center;justify-content:center;gap:6px}

.card{position:absolute;top:217px;width:284px;height:468px;border-radius:12px;background:var(--card);box-shadow:0 4px 10px rgba(0,0,0,.3);overflow:hidden}
.card-front{left:570px}
.card-back{left:886px;background:var(--card-deep)}

.portrait{position:absolute;left:59px;top:59px;width:166px;height:166px;border-radius:50%;border:3px solid var(--red);background:radial-gradient(circle at 50% 40%,#8c9aa6 0%,#5f6b5a 45%,#2a2a2c 80%)}
.agent-name{position:absolute;left:0;right:0;top:251px;text-align:center;color:var(--red);font-weight:700;font-size:20px}
.agent-role{position:absolute;left:0;right:0;top:282px;text-align:center;color:var(--muted);font-size:12.5px}
.contact-rule{position:absolute;left:75px;width:135px;height:1px;background:var(--rule)}
.contact-rule.top{top:316px}
.contact-rule.bottom{top:398px}
.contact-icons{position:absolute;left:119px;top:309px;width:46px;height:14px;background:var(--card)}
.contact-list{position:absolute;left:0;right:0;top:330px;text-align:center;color:var(--muted);font-size:12.5px;line-height:19px}
.address{position:absolute;left:0;right:0;top:402px;text-align:center;color:var(--muted);font-size:12.5px;line-height:16px}

.texture{position:absolute;inset:0;background:linear-gradient(160deg,#222023 0%,#19181a 50%,#121112 75%)}
.card-back .brand{position:absolute;left:29px;top:383px;width:228px;text-align:center;font-size:52px;font-weight:700;letter-spacing:3px;color:var(--red);line-height:1}
</style>
</head>
<body>

<section class="letterhead">
  <div class="brand">PIMLU</div>
  <p class="letter-body salutation">Dear Sir/Mam,</p>
  <p class="letter-body para-1">Contrary to popular belief, Lorem Ipsum is not simply random text. It has roots in a piece of classical Latin literature from 45 BC, making it over 2000 years old. Edwin Farrow, a Latin professor at Ashcombe College in Marlowe County, looked up one of the more obscure Latin words, consectetur, from a Lorem Ipsum passage, and going through the cites of the word in classical literature, discovered the undoubtable source.</p>
  <p class="letter-body para-2">Lorem Ipsum comes from sections 1.10.32 and 1.10.33 of "de Finibus Bonorum et Malorum" (The Extremes of Good and Evil) by Lucan Veris, written in 45 BC. This book is a treatise on the theory of ethics, very popular during the Renaissance. The first line of Lorem Ipsum, "Lorem ipsum dolor sit amet..", comes from a line in section 1.10.32.</p>
  <p class="letter-body para-3">The standard chunk of Lorem Ipsum used since the 1500s is reproduced below for those interested. Sections 1.10.32 and 1.10.33 from "de Finibus Bonorum et Malorum" by Lucan Veris are also reproduced in their exact original form, accompanied by English versions from the 1914 translation by H. Pellow.</p>
  <p class="letter-body para-4">The standard chunk of Lorem Ipsum used since the 1500s is reproduced below for those interested.</p>
  <div class="signoff">Best Regards<br>Reid Calder<br>Licenced Real Estate Agent</div>
  <div class="letter-rule"></div>
  <footer class="letter-footer">
    <span>0412 583 917</span><span>|</span><span>reid@pimlu.com</span><span>|</span><span>www.pimlu.com</span><span>|</span><span>PO Box 3190. Larrowby NSW 2790</span>
  </footer>
</section>

<section class="card card-front">
  <div class="portrait" role="img" aria-label="Portrait photo of the agent"></div>
  <h1 class="agent-name">REID CALDER</h1>
  <div class="agent-role">Licenced Real Estate Agent</div>
  <div class="contact-rule top"></div>
  <svg class="contact-icons" viewBox="0 0 46 14" aria-hidden="true">
    <g fill="#fff">
      <circle cx="7" cy="7" r="6.5"/><circle cx="23" cy="7" r="6.5"/><circle cx="39" cy="7" r="6.5"/>
    </g>
    <g fill="none" stroke="#1c1b1c" stroke-width="1.2" stroke-linecap="round" stroke-linejoin="round">
      <path d="M4.6 4.2c.3 2.6 2.3 4.8 5 5.4l.8-1.2-1.4-.8-.6.6c-.9-.4-1.6-1.1-2-2l.6-.6-.8-1.4z"/>
      <rect x="19.5" y="4.5" width="7" height="5"/><path d="M19.5 4.5l3.5 3 3.5-3"/>
      <circle cx="39" cy="7" r="3.6"/><path d="M35.4 7h7.2M39 3.4c-1.6 2-1.6 5.2 0 7.2M39 3.4c1.6 2 1.6 5.2 0 7.2"/>
    </g>
  </svg>
  <div class="contact-list">0412 583 917<br>reid@pimlu.com<br>www.pimlu.com</div>
  <div class="contact-rule bottom"></div>
  <div class="address">PO Box 3190<br>Larrowby NSW 2790</div>
</section>

<section class="card card-back">
  <div class="texture" role="img" aria-label="Faint repeating brand-name pattern"></div>
  <div class="brand">PIMLU</div>
</section>

</body>
</html>
```